Mindfulness School for Children -- Business Cards

We're looking for business cards for our school directors and owners. We're a mindfulness school for children called little lanterns. Attached are our logos/icons.

```html
<!DOCTYPE html>
<html lang="en">
<head>
<meta charset="utf-8">
<title>little lanterns – business cards</title>
<link href="https://fonts.googleapis.com/css2?family=Raleway:wght@400;500&family=Arimo:wght@400&display=swap" rel="stylesheet">
<style>
  :root{
    --canvas:#9c9c9c;
    --teal-light:#7fcdd2;
    --teal-mid:#68c1bd;
    --teal-deep:#5fb9ac;
    --mint:#8fd3a8;
    --sky:#52b4cc;
    --icon-teal:#6cc4b3;
    --paper:#f7f7f7;
    --paper-shade:#ececec;
    --ink:#5a5a5a;
    --rule:#9a9a9a;
    --white:#ffffff;
  }
  *{margin:0;padding:0;box-sizing:border-box}
  html,body{width:1200px;height:1200px;overflow:hidden}
  body{background:var(--canvas);position:relative;font-family:'Arimo',Arial,sans-serif}

  .card{position:absolute;top:303px;height:594px}

  .card--front{
    left:201px;width:369px;
    background:
      radial-gradient(ellipse at 50% 25%, rgba(140,210,220,.7), transparent 60%),
      linear-gradient(180deg,var(--teal-light) 0%,var(--teal-mid) 55%,var(--teal-deep) 100%);
  }
  .front-brand{
    position:absolute;left:0;right:0;top:330px;
    display:flex;flex-direction:column;align-items:center;gap:18px;
  }
  .front-brand__dot{width:46px;height:46px;border-radius:50%;background:var(--white)}
  .front-brand__name{
    font-family:'Raleway',sans-serif;font-weight:500;font-size:34px;color:var(--white);
  }
  .front-url{
    position:absolute;left:0;right:0;top:536px;text-align:center;
    color:var(--white);font-size:15px;letter-spacing:2.2px;
  }

  .card--back{
    left:599px;width:364px;
    background:
      radial-gradient(ellipse at 40% 40%, var(--paper-shade), transparent 55%),
      var(--paper);
  }
  .back-logo{
    position:absolute;left:0;right:0;top:140px;text-align:center;
    font-family:'Raleway',sans-serif;font-weight:500;font-size:34px;color:var(--teal-deep);
  }
  .person{position:absolute;left:0;right:0;top:330px;text-align:center}
  .person__name{font-family:'Raleway',sans-serif;font-weight:500;font-size:27px;line-height:1}
  .person__first{color:var(--mint)}
  .person__last{color:var(--sky)}
  .person__title{font-size:16.5px;color:var(--ink);margin-top:5px}

  .icon-row{
    position:absolute;left:87px;width:190px;top:395px;
    display:flex;align-items:center;gap:4px;
  }
  .icon-row__rule{flex:1;height:1px;background:var(--rule)}
  .icon-row__icon{width:25px;height:25px;border-radius:3px;background:var(--icon-teal);display:flex;align-items:center;justify-content:center}

  .contact{position:absolute;left:0;right:0;text-align:center;color:var(--ink);font-size:16.5px;line-height:21.5px}
  .contact--lines{top:431px}
  .contact__accent{color:var(--sky)}
  .contact-rule{position:absolute;left:88px;width:195px;top:507px;height:1px;background:var(--rule)}
  .contact--address{top:518px}
</style>
</head>
<body>

<section class="card card--front">
  <div class="front-brand">
    <div class="front-brand__dot"></div>
    <div class="front-brand__name">little lanterns</div>
  </div>
  <div class="front-url">www.littlelanterns.com</div>
</section>

<section class="card card--back">
  <div class="back-logo">little lanterns</div>

  <div class="person">
    <div class="person__name"><span class="person__first">Daniel</span> <span class="person__last">Hart</span></div>
    <div class="person__title">Managing Director</div>
  </div>

  <div class="icon-row">
    <span class="icon-row__rule"></span>
    <span class="icon-row__icon">
      <svg width="15" height="15" viewBox="0 0 16 16"><path d="M2 6c0-2 2-3 6-3s6 1 6 3v1h-3V5.5H5V7H2z M4 8h8l1 5H3z" fill="#fff"/></svg>
    </span>
    <span class="icon-row__icon">
      <svg width="15" height="11" viewBox="0 0 16 12"><rect x="0.5" y="0.5" width="15" height="11" fill="none" stroke="#fff"/><path d="M0.5 0.5L8 7l7.5-6.5M0.5 11.5L6 6M15.5 11.5L10 6" fill="none" stroke="#fff"/></svg>
    </span>
    <span class="icon-row__icon">
      <svg width="16" height="16" viewBox="0 0 16 16"><circle cx="8" cy="8" r="7" fill="#fff"/><path d="M5 4c2 0 3 1 2 3s1 2 0 4M10 3c1 2 3 3 2 6" fill="none" stroke="#6cc4b3" stroke-width="1.6"/></svg>
    </span>
    <span class="icon-row__rule"></span>
  </div>

  <div class="contact contact--lines">
    <div>044-555 018 272</div>
    <div>hello@lanternmail.com</div>
    <div>www.<span class="contact__accent">littlelanterns</span>.com</div>
  </div>
  <div class="contact-rule"></div>
  <div class="contact contact--address">
    <div>37, Willow Lane North</div>
    <div>45820,Brookvale Hills</div>
  </div>
</section>

</body>
</html>
```